Golden Coat All-Purpose Breading Bag Design

Our client, Halvern Food Products, is looking to re-design the packaging for their product, Pellham's Golden Coat. Goldn Coat is an all-purpose food breading mix.

Halvern Foods has a registered trademark for this product, but they have not been using it for this particular 10 pound bag. They want to get the trademark onto the bag and also give the bag an updated look. They would like to continue to use the same red and blue colors. This 10 pound bag is not available on store shelves; it is sold to food service distributors who sell to restaurants.

All of the copy on the existing bag is still relevant, so we will want to incoprporate it into the bag design. Once these bags are filled with product, the tops get folded over about 1 inch and then sewn shut with thread.

Eventually, we will need the design applied to the Bag Template file attached, but that isn't important until a design is selected.

Target Market(s)

Restaurants

Industry/Entity Type

Food Manufacturing

Colors
0054AA
0677BA
7BADD7
CADEEF
E8F1F8
EB3D1F
EC4F4E
F09395
F8D3D4
FCEDEE

Requirements
Must have
• Trademark introduced to the design

```html
<!DOCTYPE html>
<html lang="en">
<head>
<meta charset="utf-8">
<title>Pellham's Golden Coat – All Purpose Breading Bag</title>
<link href="https://fonts.googleapis.com/css2?family=Fira+Sans+Condensed:ital,wght@1,700;1,800&family=Montserrat:wght@700;800&family=Oswald:wght@600&display=swap" rel="stylesheet">
<style>
  :root {
    --brand-blue: #213a87;
    --brand-red: #d02027;
    --wheat-lavender: #c7cde3;
    --ground-band: #c5cbe0;
    --soft-blue-text: #b9c4e8;
    --paper: #ffffff;
  }
  html, body {
    margin: 0;
    width: 1200px;
    height: 667px;
    overflow: hidden;
    background: var(--paper);
  }
  .bag-front {
    position: absolute;
    left: 50%;
    top: 14px;
    transform: translateX(-50%);
    width: 407px;
    height: 640px;
    display: block;
  }
  .tagline { font-family: "Fira Sans Condensed", sans-serif; font-style: italic; font-weight: 800; font-size: 27px; fill: var(--brand-blue); }
  .tagline-accent { fill: var(--brand-red); }
  .brand-name { font-family: "Montserrat", sans-serif; font-weight: 800; fill: var(--paper); }
  .descriptor { font-family: "Montserrat", sans-serif; font-weight: 800; font-size: 25px; fill: var(--paper); letter-spacing: 1px; }
  .claim { font-family: "Oswald", sans-serif; font-weight: 600; font-size: 29px; fill: var(--paper); }
  .claim-detail { font-family: "Fira Sans Condensed", sans-serif; font-style: italic; font-weight: 700; font-size: 17px; fill: var(--soft-blue-text); letter-spacing: 1px; }
  .ingredients { font-family: "Montserrat", sans-serif; font-weight: 700; font-size: 13.5px; fill: var(--paper); letter-spacing: 1.6px; }
  .net-weight { font-family: "Montserrat", sans-serif; font-weight: 800; font-size: 19px; fill: var(--paper); letter-spacing: 2px; }
  .wheat-area { fill: var(--wheat-lavender); }
</style>
</head>
<body>
<svg class="bag-front" viewBox="95 230 700 1100" xmlns="http://www.w3.org/2000/svg">
  <!-- ground band -->
  <rect x="107" y="1122" width="665" height="198" fill="var(--ground-band)"/>

  <!-- wheat stalks -->
  <g>
    <rect class="wheat-area" x="100" y="830" width="70" height="290" rx="30" role="img" aria-label="Stylised wheat stalk illustration"/>
    <rect class="wheat-area" x="182" y="880" width="62" height="240" rx="28" role="img" aria-label="Stylised wheat stalk illustration"/>
    <rect class="wheat-area" x="637" y="870" width="62" height="250" rx="28" role="img" aria-label="Stylised wheat stalk illustration"/>
    <rect class="wheat-area" x="707" y="830" width="78" height="290" rx="32" role="img" aria-label="Stylised wheat stalk illustration"/>
  </g>

  <!-- tagline -->
  <g transform="rotate(-7 445 290)">
    <text class="tagline" x="445" y="278" text-anchor="middle">CHICKEN FRIED THE GOLDEN COAT WAY</text>
    <text class="tagline" x="445" y="310" text-anchor="middle">IS FRIED CHICKEN <tspan class="tagline-accent">THE RIGHT WAY.</tspan></text>
    <line x1="478" y1="320" x2="612" y2="320" stroke="var(--brand-red)" stroke-width="3" stroke-linecap="round"/>
  </g>

  <!-- upper blue block -->
  <path d="M240 382 Q440 338 645 350 L645 520 L240 520 Z" fill="var(--brand-blue)"/>
  <text class="brand-name" x="445" y="452" text-anchor="middle" font-size="52">PELLHAM'S</text>

  <!-- lower blue block -->
  <rect x="252" y="795" width="376" height="445" fill="var(--brand-blue)"/>

  <!-- red banner -->
  <path d="M150 542 Q440 482 728 497 L714 588 L724 590 L702 705 L692 707 L686 795 Q440 792 190 832 L180 746 L166 744 L160 642 L170 640 Z" fill="var(--brand-red)"/>
  <text class="brand-name" x="440" y="660" text-anchor="middle" font-size="108">GOLDEN</text>
  <text class="descriptor" x="397" y="717" text-anchor="end">THE ALL</text>
  <text class="descriptor" x="397" y="742" text-anchor="end">PURPOSE</text>
  <text class="descriptor" x="397" y="768" text-anchor="end">BREADING</text>
  <text class="brand-name" x="410" y="772" font-size="92">COAT</text>

  <!-- claims and copy -->
  <text class="claim" x="441" y="870" text-anchor="middle">SEALS JUICE IN - GREASE OUT</text>
  <text class="claim-detail" x="441" y="893" text-anchor="middle">COOKS TWO-POUND CHICKEN WELL DONE</text>
  <text class="claim-detail" x="441" y="915" text-anchor="middle">IN 10 MINUTES (DEEP FAT).</text>
  <line x1="322" y1="945" x2="562" y2="945" stroke="var(--paper)" stroke-width="2"/>
  <text class="ingredients" x="441" y="983" text-anchor="middle">INGREDIENTS: FLOUR, SALT, NON-FAT</text>
  <text class="ingredients" x="441" y="1005" text-anchor="middle">MILK SOLIDS, EGG YOLK, BAKING</text>
  <text class="ingredients" x="441" y="1027" text-anchor="middle">POWDER, CORN STARCH, SUGAR AND</text>
  <text class="ingredients" x="441" y="1049" text-anchor="middle">PEPPER.</text>
  <text class="net-weight" x="441" y="1122" text-anchor="middle">NET WT. 10 LBS.</text>
</svg>
</body>
</html>
```